Business Card Design for Marketing Firm

Looking for business card design for higher end marketing firm. Clean but impressionable/trendy. We are a marketing firm that represents manufacturers in the foodservice equipment and supply industry. Our customers are end users such has hotels, restaurants, country clubs, convention centers and casinos as well as distributors of restaurants supplies and equipment, and manufacturers of foodservice equipment and supplies.
Target Market(s)
Hotels, Restaurants, Supply & Equipment Distributors, Foodservice Manufacturers
Industry/Entity Type
Foodservice/Hospitality
Contact Information for Business Card
Name, Title, Contact Number, Email, Website, Social Media, Address
Requirements
Must have
- Clean & Simple but Serious and Impressionable

```html
<!DOCTYPE html>
<html lang="en">
<head>
<meta charset="utf-8">
<title>Northgate Supply Partners – Business Card</title>
<link rel="stylesheet" href="https://fonts.googleapis.com/css2?family=Open+Sans:wght@400;700&display=swap">
<style>
  :root {
    --brand-blue: #2a2c7a;
    --paper: #ffffff;
    --backdrop: #e8e8ec;
    --ink-soft: #1c1c2e;
    --card-w: 540px;
    --card-h: 310px;
  }
  * { box-sizing: border-box; margin: 0; padding: 0; }
  html, body {
    width: 1200px; height: 834px; overflow: hidden;
    background: var(--backdrop);
    font-family: "Open Sans", sans-serif;
  }
  .canvas {
    width: 1200px; height: 834px;
    display: flex; align-items: center; justify-content: center; gap: 40px;
  }
  .card {
    position: relative;
    width: var(--card-w); height: var(--card-h);
    border-radius: 28px; overflow: hidden;
    box-shadow: 0 10px 28px rgba(20, 20, 60, .18);
  }

  /* Wordmark: one font, one weight, one colour, plain square */
  .wordmark {
    display: flex; align-items: center; gap: 9px;
    font-family: "Open Sans", sans-serif; font-weight: 700;
    letter-spacing: .01em; white-space: nowrap;
  }
  .wordmark__square { width: 12px; height: 12px; flex: none; background: currentColor; }

  /* Front */
  .card--front { background: var(--paper); }
  .card__wave { position: absolute; inset: 0; }
  .card--front .wordmark {
    position: absolute; left: 34px; top: 40px;
    color: var(--brand-blue); font-size: 16px;
  }
  .person { position: absolute; right: 30px; top: 96px; text-align: right; }
  .person__name {
    color: var(--brand-blue); font-weight: 700; font-size: 20px; letter-spacing: .02em;
  }
  .person__title { color: var(--ink-soft); font-size: 12.5px; margin-top: 1px; }

  .social {
    position: absolute; left: 40px; top: 200px;
    display: flex; gap: 10px; list-style: none;
  }
  .social__dot { width: 9px; height: 9px; border-radius: 50%; background: var(--paper); }

  .contact {
    position: absolute; right: 110px; bottom: 18px; list-style: none;
    color: var(--paper); font-size: 11.5px; line-height: 1.4; text-align: right;
  }
  .contact__address { margin-bottom: 5px; }
  .contact__item { display: flex; align-items: center; justify-content: flex-end; gap: 7px; }
  .contact__icon { width: 11px; height: 11px; flex: none; }

  /* Back */
  .card--back {
    background: var(--brand-blue);
    display: flex; align-items: center; justify-content: center;
  }
  .card--back .wordmark { color: var(--paper); font-size: 28px; gap: 14px; }
  .card--back .wordmark__square { width: 20px; height: 20px; }
</style>
</head>
<body>
<main class="canvas">

  <article class="card card--front" aria-label="Business card front">
    <svg class="card__wave" viewBox="0 0 540 310" width="540" height="310" aria-hidden="true">
      <path d="M0,138 C210,126 420,140 540,200 L540,310 L0,310 Z" fill="var(--brand-blue)"/>
      <path d="M12,160 C220,150 420,165 540,230" fill="none" stroke="var(--paper)" stroke-width="2.5"/>
    </svg>

    <div class="wordmark">
      <span class="wordmark__square" aria-hidden="true"></span>
      Northgate Supply Partners
    </div>

    <div class="person">
      <p class="person__name">DANIEL REYES</p>
      <p class="person__title">Managing Director</p>
    </div>

    <ul class="social" aria-label="Social media">
      <li class="social__dot"></li>
      <li class="social__dot"></li>
      <li class="social__dot"></li>
      <li class="social__dot"></li>
      <li class="social__dot"></li>
    </ul>

    <ul class="contact">
      <li class="contact__address">Your address, City<br>State, Zip 1234</li>
      <li class="contact__item">123 456 789
        <svg class="contact__icon" viewBox="0 0 12 12" aria-hidden="true"><path d="M3 1 L5 3.5 L4 5 C4.8 6.6 5.6 7.4 7 8 L8.5 7 L11 9 L9.5 11 C5 10.5 1.5 7 1 2.5 Z" fill="var(--paper)"/></svg>
      </li>
      <li class="contact__item">info@yourmail.com
        <svg class="contact__icon" viewBox="0 0 12 12" aria-hidden="true"><rect x="1" y="2.5" width="10" height="7" rx="1" fill="var(--paper)"/><path d="M1.5 3 L6 6.5 L10.5 3" fill="none" stroke="var(--brand-blue)" stroke-width="1"/></svg>
      </li>
      <li class="contact__item">www.yourwebsite.com
        <svg class="contact__icon" viewBox="0 0 12 12" aria-hidden="true"><circle cx="6" cy="6" r="5" fill="var(--paper)"/><path d="M1 6 H11 M6 1 C3.5 4 3.5 8 6 11 M6 1 C8.5 4 8.5 8 6 11" fill="none" stroke="var(--brand-blue)" stroke-width=".8"/></svg>
      </li>
    </ul>
  </article>

  <article class="card card--back" aria-label="Business card back">
    <div class="wordmark">
      <span class="wordmark__square" aria-hidden="true"></span>
      Northgate Supply Partners
    </div>
  </article>

</main>
</body>
</html>
```